Convention Display

We need a convention booth design for an 10' W x 8' T booth. It should match the look and feel of our website and our brochure design. Sample design and text via 'upload files' below. www.corvantaplume.com

```html
<!DOCTYPE html>
<html lang="en">
<head>
<meta charset="utf-8">
<title>Corvanta Plume – Convention Display</title>
<link rel="stylesheet" href="https://fonts.googleapis.com/css2?family=Questrial&family=Roboto+Condensed:wght@700&family=Kalam:wght@400&display=swap">
<style>
  :root {
    --green: #8dc63f;
    --blue: #1c75bc;
    --orange: #f7941d;
    --slate: #3e4b55;
    --ink: #1a1a1a;
    --grey-text: #7a7a7a;
    --plus: #a6a6a6;
    --frame: #d4d4d4;
    --bg: #ffffff;
  }
  * { margin: 0; padding: 0; box-sizing: border-box; }
  html, body { width: 1200px; height: 848px; overflow: hidden; background: var(--bg); }
  .canvas { position: relative; width: 1200px; height: 848px; font-family: "Questrial", sans-serif; }
  .booth-panel {
    position: absolute; left: 71px; top: 75px; width: 1063px; height: 642px;
    border: 2px solid var(--frame); background: var(--bg); overflow: hidden;
  }
  .hero-photo {
    position: absolute; left: 600px; top: 3px; width: 450px; height: 460px; z-index: 0;
    background: radial-gradient(ellipse 60% 58% at 58% 46%, #b8b8b8 0%, #d6d6d6 45%, #f2f2f2 75%, rgba(255,255,255,0) 100%);
  }
  .tagline, .brand-name, .brand-subtitle, .layers-diagram, .engagement-line, .benefits { z-index: 1; }
  .tagline { position: absolute; left: 34px; top: 10px; font-size: 27px; white-space: nowrap; }
  .tagline .personal { color: var(--green); }
  .tagline .shared { color: var(--blue); margin-left: 8px; }
  .tagline .relevant { color: var(--orange); margin-left: 4px; }
  .brand-name {
    position: absolute; left: 52px; top: 118px; font-size: 52px; color: var(--slate);
    letter-spacing: -1px; white-space: nowrap; line-height: 1;
  }
  .brand-subtitle {
    position: absolute; left: 169px; top: 184px; font-size: 19px; color: var(--ink);
    letter-spacing: 1.2px; white-space: nowrap;
  }
  .layers-diagram { position: absolute; left: 62px; top: 240px; width: 520px; height: 134px; }
  .layer-word { font-family: "Kalam", cursive; font-size: 44px; fill: #fff; text-anchor: middle; }
  .engagement-line {
    position: absolute; left: 160px; top: 385px; font-family: "Roboto Condensed", sans-serif;
    font-weight: 700; font-size: 29px; color: var(--ink); white-space: nowrap;
  }
  .engagement-line .accent { color: var(--green); }
  .benefits { position: absolute; left: 0; top: 0; width: 100%; height: 100%; }
  .benefit {
    position: absolute; font-size: 27px; color: var(--grey-text); letter-spacing: -0.6px; white-space: nowrap;
  }
</style>
</head>
<body>
<div class="canvas">
  <section class="booth-panel">
    <div class="hero-photo" role="img" aria-label="Smiling doctor in a white coat with a stethoscope, holding a smartphone showing the patient portal app"></div>

    <p class="tagline">
      <span class="personal">make it personal</span>
      <span class="shared">make it shared</span>
      <span class="relevant">make it relevant</span>
    </p>

    <h1 class="brand-name">corvanta plume</h1>
    <p class="brand-subtitle">A NEW GENERATION PATIENT PORTAL</p>

    <svg class="layers-diagram" viewBox="0 0 520 134" aria-label="me plus we plus info">
      <circle cx="66" cy="66" r="58" fill="var(--green)"/>
      <text class="layer-word" x="66" y="80">me</text>
      <rect x="135" y="58" width="38" height="14" fill="var(--plus)"/>
      <rect x="147" y="46" width="14" height="38" fill="var(--plus)"/>
      <circle cx="245" cy="66" r="58" fill="var(--blue)"/>
      <text class="layer-word" x="245" y="80">we</text>
      <rect x="321" y="58" width="38" height="14" fill="var(--plus)"/>
      <rect x="333" y="46" width="14" height="38" fill="var(--plus)"/>
      <circle cx="433" cy="66" r="58" fill="var(--orange)"/>
      <text class="layer-word" x="433" y="80">info</text>
    </svg>

    <p class="engagement-line"><span class="accent">3 LAYERS</span> TO ENGAGEMENT</p>

    <div class="benefits">
      <span class="benefit" style="left:15px; top:493px;">Improve Satisfaction</span>
      <span class="benefit" style="left:127px; top:527px;">Integrate Your PHR</span>
      <span class="benefit" style="left:54px; top:561px;">Change Behavior</span>

      <span class="benefit" style="left:369px; top:493px;">Streamline Care</span>
      <span class="benefit" style="left:449px; top:527px;">Meet Meaningful Use</span>
      <span class="benefit" style="left:432px; top:561px;">Capture Analytics</span>

      <span class="benefit" style="left:722px; top:493px;">Increase Donations</span>
      <span class="benefit" style="left:835px; top:527px;">Incorporate Staff</span>
      <span class="benefit" style="left:750px; top:561px;">Grow Your Community</span>
    </div>
  </section>
</div>
</body>
</html>
```